DJ Colm Vetter

I'm looking for a professional but still artsy/progressive design. I come from a hip hop/club DJ background playing a lot of underground music but have switched to doing more corporate parties and weddings recently. I am all about keeping the dancefloor moving and emotionally connecting with the crowd. I'd like a trendy/updated color palette. Something that's clean enough that looks professional but also trendy enough to convey that by the end of the night we'll be sweatily dancing to the latest hits. Some designers/artists I like: Tarn Olquist, Pavel Remy, Wendell Quarrie, Lumeno 7400, Silas Dravin.

```html
<!DOCTYPE html>
<html lang="en">
<head>
<meta charset="utf-8">
<title>DJ Colm Vetter – Business Cards</title>
<link rel="stylesheet" href="https://fonts.googleapis.com/css2?family=Oswald:wght@500&family=Open+Sans:wght@400;600&display=swap">
<style>
  :root{
    --page:#e4e4e4;
    --card:#f6f6f6;
    --ink:#2f2e2f;
    --band:#333233;
    --band-text:#f2f2f2;
    --gold:#c9a415;
    --grey:#8a8a8a;
  }
  *{box-sizing:border-box;margin:0;padding:0}
  html,body{width:1200px;height:2400px;overflow:hidden}
  body{background:var(--page);position:relative;font-family:"Open Sans",Arial,sans-serif}

  .card{position:absolute;background:var(--card);overflow:hidden;box-shadow:0 2px 6px rgba(0,0,0,.08)}
  .card--gold{--accent:var(--gold)}
  .card--grey{--accent:var(--grey)}

  .card--portrait{width:479px;height:842px;top:106px}
  .card--portrait.card--gold{left:92px}
  .card--portrait.card--grey{left:637px}

  .card--landscape{width:868px;height:462px;left:166px}
  .card--landscape.card--gold{top:1198px}
  .card--landscape.card--grey{top:1777px}

  .brand-mark{position:absolute;border-radius:50%;background:var(--accent)}
  .card--portrait .brand-mark{width:210px;height:210px;left:134px;top:150px}
  .card--landscape .brand-mark{width:72px;height:72px;left:160px;top:165px}

  .brand-name{position:absolute;font-family:"Oswald","Arial Narrow",sans-serif;font-weight:500;color:var(--ink);letter-spacing:1px;white-space:nowrap;line-height:1}
  .card--portrait .brand-name{left:0;right:0;text-align:center;top:410px;font-size:62px}
  .card--landscape .brand-name{left:260px;top:168px;font-size:62px}

  .contact-band{position:absolute;left:0;right:0;background:var(--band);color:var(--band-text)}
  .card--portrait .contact-band{top:660px;height:150px}
  .card--landscape .contact-band{top:371px;height:64px}

  .contact-item{position:absolute;display:flex;align-items:center;gap:10px;font-size:12.5px;line-height:1.35;white-space:nowrap}
  .icon{width:28px;height:28px;flex:none;display:block}
  .icon-disc{fill:var(--accent)}
  .icon-glyph{fill:none;stroke:var(--band);stroke-width:1.7;stroke-linejoin:round;stroke-linecap:round}

  .card--portrait .contact-item--address{left:44px;top:30px}
  .card--portrait .contact-item--email{left:250px;top:37px}
  .card--portrait .contact-item--phone{left:44px;top:88px}
  .card--portrait .contact-item--web{left:250px;top:95px}

  .card--landscape .contact-item{top:14px}
  .card--landscape .contact-item--address{left:40px}
  .card--landscape .contact-item--email{left:230px;top:18px}
  .card--landscape .contact-item--phone{left:410px}
  .card--landscape .contact-item--web{left:604px;top:18px}
</style>
</head>
<body>

<section class="card card--portrait card--gold">
  <span class="brand-mark" aria-hidden="true"></span>
  <h1 class="brand-name">DJ COLM VETTER</h1>
  <div class="contact-band">
    <div class="contact-item contact-item--address"><svg class="icon" viewBox="0 0 28 28" aria-hidden="true"><circle class="icon-disc" cx="14" cy="14" r="14"/><path class="icon-glyph" d="M8 14 L14 8.5 L20 14 M10 13 V19.5 H18 V13"/></svg><span>Street Address Here<br>Singapore, 2222</span></div>
    <div class="contact-item contact-item--email"><svg class="icon" viewBox="0 0 28 28" aria-hidden="true"><circle class="icon-disc" cx="14" cy="14" r="14"/><path class="icon-glyph" d="M8 10 H20 V18 H8 Z M8 10 L14 15 L20 10"/></svg><span>urname@email.com</span></div>
    <div class="contact-item contact-item--phone"><svg class="icon" viewBox="0 0 28 28" aria-hidden="true"><circle class="icon-disc" cx="14" cy="14" r="14"/><path class="icon-glyph" d="M10 8 L12.5 8 L13.5 11 L12 12.3 C12.8 14 14 15.2 15.7 16 L17 14.5 L20 15.5 L20 18 C20 19 19 19.8 18 19.6 C12.5 18.8 9.2 15.5 8.4 10 C8.2 9 9 8 10 8 Z"/></svg><span>+18 2555 0140 3306<br>+18 2555 0140 3306</span></div>
    <div class="contact-item contact-item--web"><svg class="icon" viewBox="0 0 28 28" aria-hidden="true"><circle class="icon-disc" cx="14" cy="14" r="14"/><circle class="icon-glyph" cx="14" cy="14" r="6.2"/><path class="icon-glyph" d="M7.8 14 H20.2 M14 7.8 C11.5 10.5 11.5 17.5 14 20.2 C16.5 17.5 16.5 10.5 14 7.8"/></svg><span>www.websitename.com</span></div>
  </div>
</section>

<section class="card card--portrait card--grey">
  <span class="brand-mark" aria-hidden="true"></span>
  <h1 class="brand-name">DJ COLM VETTER</h1>
  <div class="contact-band">
    <div class="contact-item contact-item--address"><svg class="icon" viewBox="0 0 28 28" aria-hidden="true"><circle class="icon-disc" cx="14" cy="14" r="14"/><path class="icon-glyph" d="M8 14 L14 8.5 L20 14 M10 13 V19.5 H18 V13"/></svg><span>Street Address Here<br>Singapore, 2222</span></div>
    <div class="contact-item contact-item--email"><svg class="icon" viewBox="0 0 28 28" aria-hidden="true"><circle class="icon-disc" cx="14" cy="14" r="14"/><path class="icon-glyph" d="M8 10 H20 V18 H8 Z M8 10 L14 15 L20 10"/></svg><span>urname@email.com</span></div>
    <div class="contact-item contact-item--phone"><svg class="icon" viewBox="0 0 28 28" aria-hidden="true"><circle class="icon-disc" cx="14" cy="14" r="14"/><path class="icon-glyph" d="M10 8 L12.5 8 L13.5 11 L12 12.3 C12.8 14 14 15.2 15.7 16 L17 14.5 L20 15.5 L20 18 C20 19 19 19.8 18 19.6 C12.5 18.8 9.2 15.5 8.4 10 C8.2 9 9 8 10 8 Z"/></svg><span>+18 2555 0140 3306<br>+18 2555 0140 3306</span></div>
    <div class="contact-item contact-item--web"><svg class="icon" viewBox="0 0 28 28" aria-hidden="true"><circle class="icon-disc" cx="14" cy="14" r="14"/><circle class="icon-glyph" cx="14" cy="14" r="6.2"/><path class="icon-glyph" d="M7.8 14 H20.2 M14 7.8 C11.5 10.5 11.5 17.5 14 20.2 C16.5 17.5 16.5 10.5 14 7.8"/></svg><span>www.websitename.com</span></div>
  </div>
</section>

<section class="card card--landscape card--gold">
  <span class="brand-mark" aria-hidden="true"></span>
  <h1 class="brand-name">DJ COLM VETTER</h1>
  <div class="contact-band">
    <div class="contact-item contact-item--address"><svg class="icon" viewBox="0 0 28 28" aria-hidden="true"><circle class="icon-disc" cx="14" cy="14" r="14"/><path class="icon-glyph" d="M8 14 L14 8.5 L20 14 M10 13 V19.5 H18 V13"/></svg><span>Street Address Here<br>Singapore, 2222</span></div>
    <div class="contact-item contact-item--email"><svg class="icon" viewBox="0 0 28 28" aria-hidden="true"><circle class="icon-disc" cx="14" cy="14" r="14"/><path class="icon-glyph" d="M8 10 H20 V18 H8 Z M8 10 L14 15 L20 10"/></svg><span>urname@email.com</span></div>
    <div class="contact-item contact-item--phone"><svg class="icon" viewBox="0 0 28 28" aria-hidden="true"><circle class="icon-disc" cx="14" cy="14" r="14"/><path class="icon-glyph" d="M10 8 L12.5 8 L13.5 11 L12 12.3 C12.8 14 14 15.2 15.7 16 L17 14.5 L20 15.5 L20 18 C20 19 19 19.8 18 19.6 C12.5 18.8 9.2 15.5 8.4 10 C8.2 9 9 8 10 8 Z"/></svg><span>+18 2555 0140 3306<br>+18 2555 0140 3306</span></div>
    <div class="contact-item contact-item--web"><svg class="icon" viewBox="0 0 28 28" aria-hidden="true"><circle class="icon-disc" cx="14" cy="14" r="14"/><circle class="icon-glyph" cx="14" cy="14" r="6.2"/><path class="icon-glyph" d="M7.8 14 H20.2 M14 7.8 C11.5 10.5 11.5 17.5 14 20.2 C16.5 17.5 16.5 10.5 14 7.8"/></svg><span>www.websitename.com</span></div>
  </div>
</section>

<section class="card card--landscape card--grey">
  <span class="brand-mark" aria-hidden="true"></span>
  <h1 class="brand-name">DJ COLM VETTER</h1>
  <div class="contact-band">
    <div class="contact-item contact-item--address"><svg class="icon" viewBox="0 0 28 28" aria-hidden="true"><circle class="icon-disc" cx="14" cy="14" r="14"/><path class="icon-glyph" d="M8 14 L14 8.5 L20 14 M10 13 V19.5 H18 V13"/></svg><span>Street Address Here<br>Singapore, 2222</span></div>
    <div class="contact-item contact-item--email"><svg class="icon" viewBox="0 0 28 28" aria-hidden="true"><circle class="icon-disc" cx="14" cy="14" r="14"/><path class="icon-glyph" d="M8 10 H20 V18 H8 Z M8 10 L14 15 L20 10"/></svg><span>urname@email.com</span></div>
    <div class="contact-item contact-item--phone"><svg class="icon" viewBox="0 0 28 28" aria-hidden="true"><circle class="icon-disc" cx="14" cy="14" r="14"/><path class="icon-glyph" d="M10 8 L12.5 8 L13.5 11 L12 12.3 C12.8 14 14 15.2 15.7 16 L17 14.5 L20 15.5 L20 18 C20 19 19 19.8 18 19.6 C12.5 18.8 9.2 15.5 8.4 10 C8.2 9 9 8 10 8 Z"/></svg><span>+18 2555 0140 3306<br>+18 2555 0140 3306</span></div>
    <div class="contact-item contact-item--web"><svg class="icon" viewBox="0 0 28 28" aria-hidden="true"><circle class="icon-disc" cx="14" cy="14" r="14"/><circle class="icon-glyph" cx="14" cy="14" r="6.2"/><path class="icon-glyph" d="M7.8 14 H20.2 M14 7.8 C11.5 10.5 11.5 17.5 14 20.2 C16.5 17.5 16.5 10.5 14 7.8"/></svg><span>www.websitename.com</span></div>
  </div>
</section>

</body>
</html>
```